automotive repair and collision repair shop card

our company is called K.L Motor service we are a automotive repair company
we also do government inspections. the company information is on the cards. I would like you to use my new logo and create a new card and use the information from my old card. Good Luck!!

Industry/Entity Type

Car Repair

Contact Information for Business Card

Address: #417-18842 52 Ave, Surrey, BC V5K 8R3
Phone:(604) 555-0187
fax 604 555 0193
website www.klmotorworks.example

Font styles to use
Serif
Sans Serif

Requirements
Must have
• all the information
Should not have
• the owner and there name

```html
<!DOCTYPE html>
<html lang="en">
<head>
<meta charset="utf-8">
<title>K.L Motor Service – Business Card</title>
<link href="https://fonts.googleapis.com/css2?family=Oswald:wght@300;400&family=Fira+Sans+Condensed:ital,wght@0,300;1,300&display=swap" rel="stylesheet">
<style>
  :root{
    --backdrop:#d9d6d1;
    --card:#0d0d0d;
    --card-edge:#1c1c1c;
    --ink:#ffffff;
    --ink-soft:#cfcfcf;
    --photo-dark:#111111;
    --photo-mid:#3a3a3a;
    --photo-floor:#d8d8d8;
  }
  *{box-sizing:border-box;margin:0;padding:0}
  html,body{width:1200px;height:892px;overflow:hidden}
  body{background:var(--backdrop);position:relative;font-family:"Fira Sans Condensed",sans-serif;color:var(--ink)}
  .card{
    position:absolute;width:560px;height:320px;
    background:linear-gradient(135deg,var(--card-edge) 0%,var(--card) 55%);
    box-shadow:0 10px 26px rgba(0,0,0,.35);overflow:hidden;
  }
  .card--front{left:600px;top:90px}
  .card--back{left:60px;top:480px}

  .brand-title{font-family:"Oswald",sans-serif;font-weight:300;letter-spacing:.5px;text-transform:uppercase;line-height:1}
  .brand-tagline{font-style:italic;font-weight:300;color:var(--ink-soft)}
  .brand-mark{width:22px;height:22px;background:var(--ink);position:absolute}

  /* front */
  .vehicle-photo{position:absolute;left:0;top:120px;width:390px;height:200px;
    background:linear-gradient(180deg,var(--photo-dark) 0%,var(--photo-mid) 62%,var(--photo-floor) 80%,#9a9a9a 100%)}
  .card--front .brand-title{position:absolute;right:40px;top:42px;font-size:44px;text-align:right}
  .card--front .brand-tagline{position:absolute;right:46px;top:96px;font-size:17px}
  .card--front .brand-url{position:absolute;right:46px;top:124px;font-size:14px}
  .card--front .brand-mark{right:14px;top:120px}

  /* back */
  .card--back .brand-mark{left:36px;top:34px}
  .brand-block{position:absolute;left:36px;top:118px;display:inline-block}
  .card--back .brand-title{font-size:38px;white-space:nowrap}
  .card--back .brand-tagline{font-size:14px;text-align:right;margin-top:6px}
  .contact-icons{position:absolute;left:250px;top:200px;display:flex;flex-direction:column;gap:8px}
  .contact-icons svg{width:14px;height:14px;display:block}
  .contact-divider{position:absolute;left:276px;top:194px;width:2px;height:112px;background:var(--ink)}
  .contact-list{position:absolute;left:292px;top:196px;list-style:none;font-weight:300;font-size:14px;line-height:22px;white-space:nowrap}
</style>
</head>
<body>

<section class="card card--front">
  <div class="vehicle-photo" role="img" aria-label="Dark grey sports car in side profile on a white studio floor"></div>
  <h1 class="brand-title">K.L Motor Service</h1>
  <p class="brand-tagline">One Stop Repair Shop</p>
  <p class="brand-url">www.klmotorworks.example</p>
  <span class="brand-mark"></span>
</section>

<section class="card card--back">
  <span class="brand-mark"></span>
  <div class="brand-block">
    <h2 class="brand-title">K.L Motor Service</h2>
    <p class="brand-tagline">One Stop Repair Shop</p>
  </div>

  <div class="contact-icons" aria-hidden="true">
    <svg viewBox="0 0 16 16"><path d="M3 2h3l1 3-2 1a8 8 0 0 0 5 5l1-2 3 1v3c0 1-1 1-1 1A12 12 0 0 1 2 3s0-1 1-1z" fill="#fff"/></svg>
    <svg viewBox="0 0 16 16"><rect x="4" y="1" width="8" height="4" fill="#fff"/><rect x="1" y="6" width="14" height="6" rx="1" fill="#fff"/><rect x="4" y="10" width="8" height="5" fill="#fff" stroke="#000" stroke-width="1"/></svg>
    <svg viewBox="0 0 16 16" fill="none" stroke="#fff" stroke-width="1.6"><path d="M2 6a9 9 0 0 1 12 0M4.5 9a5 5 0 0 1 7 0"/><circle cx="8" cy="12.5" r="1.2" fill="#fff"/></svg>
    <svg viewBox="0 0 16 16"><rect x="1" y="3" width="14" height="10" fill="#fff"/><path d="M1 3l7 6 7-6" fill="none" stroke="#000" stroke-width="1.2"/></svg>
    <svg viewBox="0 0 16 16"><path d="M8 1a5 5 0 0 1 5 5c0 4-5 9-5 9S3 10 3 6a5 5 0 0 1 5-5z" fill="#fff"/><circle cx="8" cy="6" r="2" fill="#000"/></svg>
  </div>
  <span class="contact-divider"></span>
  <ul class="contact-list">
    <li>(604) 555-0187</li>
    <li>604 555 0193</li>
    <li>www.klmotorworks.example</li>
    <li>info@klmotorworks.example</li>
    <li>#417-18842 52 Ave, Surrey, BC V5K 8R3</li>
  </ul>
</section>

</body>
</html>
```